Postcard design to acquire new clients for my Property Management Company

I'm looking for a postcard design that I can send to prospective clients detailing information about my company and services.
Postcard should be eye catching and contain information from www.bramblecrestpm.com. I've provided a few screen shots for the most important information and my logo.
Target Market(s)
Real Estate
Industry/Entity Type
Real Estate
Font styles to use
Sans Serif
Requirements
Must have
- Must be eye catching!! this will be a direct mail piece - I'd like for the card to be read and not tossed in the trash immediately.
Design que from the logo.
A place to write / print the receipts name and address.
our physical address - 2387 Hollow Pine Road, Lubbock, TX 79852.
Should not have
- the contact information on the business card is not accurate - please use info from website.

```html
<!DOCTYPE html>
<html lang="en">
<head>
<meta charset="utf-8">
<title>Bramblecrest Property Management – Postcard</title>
<link href="https://fonts.googleapis.com/css2?family=Arimo:wght@400;700&display=swap" rel="stylesheet">
<style>
  :root {
    --brand-blue: #1f4e8c;
    --brand-navy: #1b3f73;
    --panel-blue: #265896;
    --panel-light: #3a6aa5;
    --ink: #1c1c1c;
    --paper: #ffffff;
    --stage: #ececec;
    --rule: #6b6b6b;
  }
  * { box-sizing: border-box; margin: 0; padding: 0; }
  html, body { width: 1200px; height: 1199px; overflow: hidden; }
  body {
    background: var(--stage);
    font-family: "Arimo", Arial, sans-serif;
    color: var(--ink);
    position: relative;
  }
  .postcard {
    position: absolute;
    left: 210px;
    width: 780px;
    height: 546px;
    background: var(--paper);
    box-shadow: 0 6px 16px rgba(0,0,0,.28);
    overflow: hidden;
  }
  .postcard--front { top: 40px; }
  .postcard--back { top: 613px; }
  .abs { position: absolute; }

  /* front */
  .front-shapes { left: 0; top: 0; width: 780px; height: 546px; }
  .hero-illustration {
    left: 12px; top: 36px; width: 326px; height: 265px;
    border-radius: 10px;
    background: radial-gradient(ellipse at 50% 50%, #c9d3de 0%, #a9b8c9 45%, #e8eef3 80%, rgba(255,255,255,0) 100%);
  }
  .brand-name {
    left: 350px; top: 30px;
    font-size: 31px; font-weight: 700; letter-spacing: 3px;
    color: var(--brand-blue);
  }
  .brand-tag {
    left: 352px; top: 68px;
    font-size: 14px; font-weight: 700; letter-spacing: 3.2px;
    color: var(--brand-blue);
  }
  .headline {
    left: 350px; top: 110px;
    font-size: 26px; font-weight: 700; line-height: 31px;
    color: var(--brand-blue);
  }
  .subline { left: 350px; top: 180px; font-size: 14px; }
  .badge { width: 153px; height: 92px; }
  .badge svg { position: absolute; left: 0; top: 0; }
  .badge-text {
    position: absolute; left: 0; top: 0; width: 153px;
    text-align: center; color: #fff; line-height: 1;
  }
  .badge-title { display: block; font-size: 16px; height: 17px; margin-top: 3px; white-space: nowrap; }
  .badge-note { display: block; font-size: 11px; height: 11px; margin-top: 3px; }
  .badge-rate { display: block; font-size: 24px; height: 24px; margin-top: 5px; font-weight: 700; }
  .badge-unit { display: block; font-size: 11px; height: 11px; margin-top: 3px; }
  .badge--lease { left: 354px; top: 206px; }
  .badge--full { left: 122px; top: 360px; }
  .badge--premium { left: 506px; top: 360px; }
  .features { font-size: 11.4px; line-height: 14.6px; }
  .features--lease { left: 350px; top: 309px; }
  .features--full { left: 131px; top: 462px; }
  .features--premium { left: 500px; top: 462px; }
  .tier-divider { left: 474px; top: 380px; width: 1px; height: 126px; background: #9aa8b8; }

  /* back */
  .service-panel {
    left: 0; top: 0; width: 391px; height: 546px;
    background: var(--panel-blue); color: #fff;
  }
  .panel-title {
    left: 0; top: 30px; width: 391px; text-align: center;
    font-size: 26px; font-weight: 700;
  }
  .panel-subtitle {
    left: 0; top: 63px; width: 391px; text-align: center; font-size: 13.5px;
  }
  .service { display: flex; align-items: center; gap: 8px; font-size: 21px; white-space: nowrap; }
  .service svg { flex: none; }
  .contact {
    left: 0; top: 460px; width: 391px; text-align: center;
    font-size: 16.5px; line-height: 25px;
  }
  .contact strong { font-weight: 700; }
  .stamp-box { left: 650px; top: 36px; width: 95px; height: 95px; border: 1.5px solid #333; }
  .address-line { left: 412px; width: 348px; height: 1px; background: var(--rule); }
</style>
</head>
<body>

<section class="postcard postcard--front" aria-label="Postcard front">
  <svg class="abs front-shapes" viewBox="0 0 780 546" aria-hidden="true">
    <polygon points="0,238 136,546 0,546" fill="var(--brand-blue)"/>
    <polygon points="61,372 92,546 30,546" fill="var(--paper)"/>
    <polygon points="780,238 780,546 648,546" fill="var(--brand-blue)"/>
    <polygon points="718,372 750,546 690,546" fill="var(--paper)"/>
  </svg>

  <div class="abs hero-illustration" role="img" aria-label="Illustration of a house under a magnifying glass with a key and a gold dollar sign"></div>

  <div class="abs brand-name">BRAMBLECREST</div>
  <div class="abs brand-tag">PROPERTY MANAGEMENT</div>

  <h1 class="abs headline">CHOOSE THE RIGHT PROPERTY<br>MANAGEMENT SYSTEM</h1>
  <p class="abs subline">Selecting the wrong manager could be your costliest mistake ever.</p>

  <div class="abs badge badge--lease">
    <svg width="153" height="92" viewBox="0 0 153 92" aria-hidden="true">
      <polygon points="0,20 8,0 8,20" fill="var(--brand-navy)"/>
      <polygon points="153,20 145,0 145,20" fill="var(--brand-navy)"/>
      <polygon points="12,0 141,0 141,82 76,92 12,82" fill="var(--brand-blue)"/>
    </svg>
    <div class="badge-text">
      <span class="badge-title">Lease Only</span>
      <span class="badge-note">You Just Need Tenants</span>
      <span class="badge-rate">9%</span>
      <span class="badge-unit">of annual lease</span>
    </div>
  </div>
  <p class="abs features features--lease">
    Professional Photography | Marketing &amp; Advertising<br>
    Property Showings | Tenant Screening &amp; Qualifications<br>
    Lease Execution | Move In Coordination
  </p>

  <div class="abs badge badge--full">
    <svg width="153" height="92" viewBox="0 0 153 92" aria-hidden="true">
      <polygon points="0,20 8,0 8,20" fill="var(--brand-navy)"/>
      <polygon points="153,20 145,0 145,20" fill="var(--brand-navy)"/>
      <polygon points="12,0 141,0 141,82 76,92 12,82" fill="var(--brand-blue)"/>
    </svg>
    <div class="badge-text">
      <span class="badge-title">Full Service</span>
      <span class="badge-note">Our Most Popular</span>
      <span class="badge-rate">10%</span>
      <span class="badge-unit">of monthly rent</span>
    </div>
  </div>
  <p class="abs features features--full">
    Includes Leasing Service | 24/7 Emergency Response<br>
    Move In &amp; Out Inspections | Professional Lease Enforcement<br>
    Schedule &amp; Oversee all Repairs | Pay all Invoices<br>
    Monthly &amp; Year End Statements | Annual Market Rent Analysis
  </p>

  <div class="abs tier-divider"></div>

  <div class="abs badge badge--premium">
    <svg width="153" height="92" viewBox="0 0 153 92" aria-hidden="true">
      <polygon points="0,20 8,0 8,20" fill="var(--brand-navy)"/>
      <polygon points="153,20 145,0 145,20" fill="var(--brand-navy)"/>
      <polygon points="12,0 141,0 141,82 76,92 12,82" fill="var(--brand-blue)"/>
    </svg>
    <div class="badge-text">
      <span class="badge-title">Premium Service</span>
      <span class="badge-note">Our Premier Service</span>
      <span class="badge-rate">12%</span>
      <span class="badge-unit">of monthly rent</span>
    </div>
  </div>
  <p class="abs features features--premium">
    Includes Full Service Features<br>
    Professional Video Marketing<br>
    Home Warranty Coordination<br>
    Tenant Retention Program
  </p>
</section>

<section class="postcard postcard--back" aria-label="Postcard back">
  <div class="abs service-panel">
    <svg class="abs" width="391" height="546" viewBox="0 0 391 546" aria-hidden="true" style="left:0;top:0">
      <polygon points="90,0 130,0 20,546 0,546 0,420" fill="var(--panel-light)" opacity=".45"/>
      <polygon points="140,190 300,546 0,546" fill="var(--panel-light)" opacity=".35"/>
      <polygon points="391,120 391,546 330,546" fill="var(--panel-light)" opacity=".35"/>
    </svg>

    <h2 class="abs panel-title">Discover Our Services</h2>
    <p class="abs panel-subtitle">We offer full-service property management solutions</p>

    <div class="abs service" style="left:32px;top:84px">
      <svg width="36" height="36" viewBox="0 0 36 36" aria-hidden="true"><circle cx="18" cy="18" r="16" fill="none" stroke="#fff" stroke-width="2"/><path d="M8 18 L18 9 L28 18 M11 16 V27 H25 V16" fill="none" stroke="#fff" stroke-width="2.4"/><rect x="16" y="20" width="4" height="7" fill="#fff"/></svg>
      <span>Property Marketing</span>
    </div>
    <div class="abs service" style="left:142px;top:130px">
      <svg width="36" height="36" viewBox="0 0 36 36" aria-hidden="true"><circle cx="18" cy="18" r="16" fill="none" stroke="#fff" stroke-width="2"/><circle cx="14" cy="14" r="3.5" fill="#fff"/><circle cx="22" cy="14" r="3.5" fill="#fff"/><path d="M8 25 Q14 17 20 25 Z M16 25 Q22 17 28 25 Z" fill="#fff"/></svg>
      <span>Tenant Screening</span>
    </div>
    <div class="abs service" style="left:32px;top:177px">
      <svg width="36" height="36" viewBox="0 0 36 36" aria-hidden="true"><circle cx="18" cy="18" r="16" fill="none" stroke="#fff" stroke-width="2"/><text x="18" y="25" text-anchor="middle" font-family="Arimo, sans-serif" font-size="19" font-weight="700" fill="#fff">$</text></svg>
      <span style="margin-left:6px">Rent Collection</span>
    </div>
    <div class="abs service" style="left:142px;top:220px">
      <svg width="36" height="36" viewBox="0 0 36 36" aria-hidden="true"><circle cx="18" cy="18" r="16" fill="none" stroke="#fff" stroke-width="2"/><path d="M12 26 L20 16" stroke="#fff" stroke-width="3"/><path d="M16 12 L22 10 L27 15 L22 20 Z" fill="#fff"/></svg>
      <span style="margin-left:6px">Maintenance</span>
    </div>
    <div class="abs service" style="left:32px;top:263px">
      <svg width="36" height="36" viewBox="0 0 36 36" aria-hidden="true"><circle cx="18" cy="18" r="16" fill="none" stroke="#fff" stroke-width="2"/><circle cx="16" cy="16" r="6" fill="none" stroke="#fff" stroke-width="2.4"/><path d="M20.5 20.5 L26 26" stroke="#fff" stroke-width="3"/></svg>
      <span style="margin-left:6px">Property Inspections</span>
    </div>
    <div class="abs service" style="left:142px;top:310px">
      <svg width="36" height="36" viewBox="0 0 36 36" aria-hidden="true"><circle cx="18" cy="18" r="16" fill="none" stroke="#fff" stroke-width="2"/><path d="M10 11 V25 H27" fill="none" stroke="#fff" stroke-width="1.8"/><path d="M14 23 V17 M17.5 23 V14 M21 23 V18 M24.5 23 V15" stroke="#fff" stroke-width="2"/></svg>
      <span style="margin-left:6px">Financial Reporting</span>
    </div>
    <div class="abs service" style="left:32px;top:358px">
      <svg width="36" height="36" viewBox="0 0 36 36" aria-hidden="true"><circle cx="18" cy="18" r="16" fill="none" stroke="#fff" stroke-width="2"/><path d="M18 9 L26 12 V18 Q26 24 18 28 Q10 24 10 18 V12 Z" fill="none" stroke="#fff" stroke-width="2.2"/><path d="M18 11 L24 13.5 V18 Q24 23 18 26 Z" fill="#fff"/></svg>
      <span style="margin-left:6px">Evictions</span>
    </div>
    <div class="abs service" style="left:142px;top:401px">
      <svg width="36" height="36" viewBox="0 0 36 36" aria-hidden="true"><circle cx="18" cy="18" r="16" fill="none" stroke="#fff" stroke-width="2"/><path d="M18 9 V26 M13 26 H23 M10 13 H26" stroke="#fff" stroke-width="1.8"/><path d="M7.5 20 L10 13 L12.5 20 Z M23.5 20 L26 13 L28.5 20 Z" fill="none" stroke="#fff" stroke-width="1.5"/></svg>
      <span style="margin-left:6px">Legal Guidance</span>
    </div>

    <p class="abs contact">
      2387 Hollow Pine Road, Lubbock, TX 79852<br>
      <strong>(806) 555-0147</strong> | info@bramblecrestpm.com<br>
      www.bramblecrestpm.com
    </p>
  </div>

  <div class="abs stamp-box" aria-label="Stamp area"></div>
  <div class="abs address-line" style="top:329px"></div>
  <div class="abs address-line" style="top:388px"></div>
  <div class="abs address-line" style="top:448px"></div>
  <div class="abs address-line" style="top:507px"></div>
</section>

</body>
</html>
```